KLV Plant Services

We are a heavy diesel mechanical business with additional air con certificates, remapping engine rebuilt

Contact Information for Business Card

Company Name, Director Name, Managing Director, Contact details, email and website

Font styles to use
Serif
Script

```html
<!DOCTYPE html>
<html lang="en">
<head>
<meta charset="utf-8">
<title>KLV Plant Services – Business Card</title>
<link href="https://fonts.googleapis.com/css2?family=Arimo:wght@400;700&display=swap" rel="stylesheet">
<style>
  :root {
    --navy: #020a5e;
    --white: #ffffff;
    --paper: #f4f5f7;
    --backdrop: #d9d9db;
    --rule: rgba(255,255,255,0.55);
  }
  * { margin: 0; padding: 0; box-sizing: border-box; }
  html, body {
    width: 1200px; height: 800px; overflow: hidden;
    background: var(--backdrop);
    font-family: "Arimo", Arial, sans-serif;
  }
  .sheet {
    position: relative; width: 1200px; height: 800px;
    display: flex; align-items: center; justify-content: center; gap: 48px;
  }
  .card {
    position: relative; width: 532px; height: 304px;
    border-radius: 22px; overflow: hidden;
  }
  .card--front { background: var(--navy); color: var(--white); }
  .card--back { background: var(--paper); }

  .brand { display: flex; align-items: center; gap: 12px; font-weight: 700; }
  .brand__dot { flex: none; border-radius: 50%; }
  .brand__name { line-height: 1.05; }
  .brand__name .short { display: block; }

  .card--front .brand {
    position: absolute; top: 40px; right: 48px;
  }
  .card--front .brand__dot { width: 22px; height: 22px; border: 3px solid var(--white); }
  .card--front .brand__name .short { font-size: 44px; letter-spacing: 1px; }
  .card--front .brand__name .long { font-size: 17px; }

  .divider {
    position: absolute; left: 40px; right: 40px; top: 176px;
    height: 1px; background: var(--rule);
  }
  .person { position: absolute; left: 40px; top: 128px; }
  .person__name { font-size: 23px; font-weight: 700; }
  .person__role { font-size: 15px; margin-top: 4px; }

  .contacts {
    position: absolute; left: 40px; top: 192px;
    list-style: none; font-size: 15px; line-height: 23px;
  }
  .contacts li { display: flex; align-items: center; gap: 10px; }
  .contacts svg { width: 13px; height: 13px; flex: none; }

  .address {
    position: absolute; right: 40px; top: 192px;
    font-style: normal; font-size: 15px; line-height: 23px; text-align: right;
  }

  .card--back .brand {
    position: absolute; left: 50%; top: 50%; transform: translate(-50%, -50%);
    color: var(--navy); gap: 18px;
  }
  .card--back .brand__dot { width: 34px; height: 34px; border: 4px solid var(--navy); }
  .card--back .brand__name .short { font-size: 78px; letter-spacing: 2px; }
  .card--back .brand__name .long { font-size: 28px; }
</style>
</head>
<body>
<main class="sheet">
  <section class="card card--front" aria-label="Business card front">
    <div class="brand">
      <span class="brand__dot"></span>
      <span class="brand__name"><span class="short">KLV</span><span class="long">Plant Services</span></span>
    </div>

    <div class="person">
      <p class="person__name">Owen Hartley</p>
      <p class="person__role">Managing Director</p>
    </div>

    <div class="divider"></div>

    <ul class="contacts">
      <li>
        <svg viewBox="0 0 16 16" aria-hidden="true"><path fill="#fff" d="M3.6 1.2l2.3 2.6-1.2 1.8c.9 1.9 2.4 3.4 4.3 4.3l1.8-1.2 2.6 2.3-1.3 2.6C7 13.3 2.7 9 2.6 3.1z"/></svg>
        (693) 5120-4478
      </li>
      <li>
        <svg viewBox="0 0 16 16" aria-hidden="true"><rect x="1" y="3" width="14" height="10" rx="1" fill="#fff"/><path d="M1.5 4l6.5 5 6.5-5" stroke="#020a5e" stroke-width="1.4" fill="none"/></svg>
        mail@KLV.com
      </li>
      <li>
        <svg viewBox="0 0 16 16" aria-hidden="true"><circle cx="8" cy="8" r="6.5" fill="#fff"/><path d="M1.5 8h13M8 1.5c-3 3.5-3 9.5 0 13M8 1.5c3 3.5 3 9.5 0 13" stroke="#020a5e" stroke-width="1" fill="none"/></svg>
        www.KLV.com
      </li>
    </ul>

    <address class="address">
      4120 Calder Road<br>
      Ridgefield, NY 11020
    </address>
  </section>

  <section class="card card--back" aria-label="Business card back">
    <div class="brand">
      <span class="brand__dot"></span>
      <span class="brand__name"><span class="short">KLV</span><span class="long">Plant Services</span></span>
    </div>
  </section>
</main>
</body>
</html>
```